Road Construction Company needs business cards

We would like a new business card designed for our business.

We're a road construction company based in Qld, Australia.

Can the business card please have the following information on it.

Name: Warren Halbeck
Position: General Manager
Phone: 0472 915 348
Email: Warren.halbeck@tovrin.com.au
Address: 87 Marrow Ave, Pendlebay, QLD, 4023
Website: www.tovrin.com.au

Visually we'd like the card to be professional and simple.

Attached is our logo.

Our website is www.tovrin.com.au

Target Market(s)

Men aged 25-60

Contact Information for Business Card

As listed in project description

Font styles to use
Serif

Requirements
Must have
• Large logo on back of card

```html
<!DOCTYPE html>
<html lang="en">
<head>
<meta charset="utf-8">
<title>Tovrin Business Card</title>
<link href="https://fonts.googleapis.com/css2?family=Michroma&family=Ubuntu:wght@400;500;700&display=swap" rel="stylesheet">
<style>
  :root {
    --backdrop: #2a2a2c;
    --card: #0c0c0d;
    --card-edge: #161617;
    --blue: #1466c8;
    --blue-light: #2a86e0;
    --white: #f2f2f2;
    --silver: #d9dadc;
    --divider: rgba(255,255,255,0.07);
  }
  * { margin: 0; padding: 0; box-sizing: border-box; }
  html, body { width: 1200px; height: 900px; overflow: hidden; }
  body {
    background: var(--backdrop);
    font-family: "Ubuntu", sans-serif;
    position: relative;
  }
  .card {
    position: absolute;
    left: 285px;
    width: 630px;
    height: 360px;
    background: radial-gradient(ellipse at 40% 30%, var(--card-edge), var(--card) 70%);
    border-radius: 22px;
    overflow: hidden;
  }
  .card--front { top: 60px; }
  .card--back { top: 480px; }

  .brand {
    position: absolute;
    display: flex;
    align-items: center;
    gap: 10px;
    font-family: "Ubuntu", sans-serif;
    font-weight: 700;
    letter-spacing: 2px;
  }
  .brand__mark { width: 14px; height: 14px; }
  .card--front .brand {
    left: 70px;
    top: 215px;
    font-size: 42px;
    color: var(--blue);
  }
  .card--front .brand__mark { background: var(--blue); }
  .card--back .brand {
    left: 50%;
    top: 50%;
    transform: translate(-50%, -50%);
    font-size: 64px;
    color: var(--silver);
  }
  .card--back .brand__mark { background: var(--silver); width: 18px; height: 18px; }

  .divider {
    position: absolute;
    left: 318px;
    top: 50px;
    width: 1px;
    height: 260px;
    background: var(--divider);
  }
  .details {
    position: absolute;
    left: 345px;
    top: 70px;
    color: var(--white);
  }
  .person__name {
    font-family: "Michroma", sans-serif;
    font-size: 17px;
    color: var(--blue);
    text-transform: uppercase;
    letter-spacing: 0.5px;
  }
  .person__role {
    font-size: 15px;
    color: var(--blue-light);
    margin-top: 2px;
  }
  .contact {
    list-style: none;
    margin-top: 22px;
    font-size: 14px;
  }
  .contact__item {
    display: flex;
    align-items: center;
    gap: 10px;
    height: 24px;
  }
  .contact__icon { width: 15px; height: 15px; fill: var(--blue); flex: none; }
  .contact__accent { color: var(--blue-light); }
  .address {
    font-style: normal;
    font-size: 14px;
    line-height: 22px;
    margin-top: 18px;
    padding-left: 25px;
  }
</style>
</head>
<body>
  <section class="card card--front">
    <div class="brand"><span class="brand__mark"></span>TOVRIN</div>
    <div class="divider"></div>
    <div class="details">
      <h1 class="person__name">Warren Halbeck</h1>
      <p class="person__role">General Manager</p>
      <ul class="contact">
        <li class="contact__item">
          <svg class="contact__icon" viewBox="0 0 24 24"><path d="M6.6 10.8a15 15 0 0 0 6.6 6.6l2.2-2.2a1 1 0 0 1 1-.25 11.4 11.4 0 0 0 3.6.57 1 1 0 0 1 1 1V20a1 1 0 0 1-1 1A17 17 0 0 1 3 4a1 1 0 0 1 1-1h3.5a1 1 0 0 1 1 1c0 1.25.2 2.45.57 3.57a1 1 0 0 1-.25 1z"/></svg>
          0472 915 348
        </li>
        <li class="contact__item">
          <svg class="contact__icon" viewBox="0 0 24 24"><path d="M2 5h20v14H2zm2 2v.5l8 5 8-5V7l-8 5z"/></svg>
          Warren.halbeck@tovrin.com.au
        </li>
        <li class="contact__item">
          <svg class="contact__icon" viewBox="0 0 24 24"><path d="M12 2a10 10 0 1 0 0 20 10 10 0 0 0 0-20zm6.9 6h-3a15 15 0 0 0-1.3-3.9A8 8 0 0 1 18.9 8zM12 4c.9 1.2 1.6 2.6 2 4h-4c.4-1.4 1.1-2.8 2-4zM4.3 14a8 8 0 0 1 0-4h3.4a16 16 0 0 0 0 4zm.8 2h3a15 15 0 0 0 1.3 3.9A8 8 0 0 1 5.1 16zm3-8h-3a8 8 0 0 1 4.3-3.9A15 15 0 0 0 8.1 8zM12 20c-.9-1.2-1.6-2.6-2-4h4c-.4 1.4-1.1 2.8-2 4zm2.3-6H9.7a14 14 0 0 1 0-4h4.6a14 14 0 0 1 0 4zm.3 5.9a15 15 0 0 0 1.3-3.9h3a8 8 0 0 1-4.3 3.9zm1.7-5.9a16 16 0 0 0 0-4h3.4a8 8 0 0 1 0 4z"/></svg>
          <span>www.<span class="contact__accent">tovrin</span>.com.au</span>
        </li>
      </ul>
      <address class="address">87 Marrow Ave<br>Pendlebay, QLD, 4023</address>
    </div>
  </section>

  <section class="card card--back">
    <div class="brand"><span class="brand__mark"></span>TOVRIN</div>
  </section>
</body>
</html>
```